Tandem Hearth Works Pty Ltd

We need business cards for a company based in Perth, we install, service and maintain fire equipment.
On the front we want a great design with our logo and a small spot for our full company name, general company email address and office number. On the back we need space for our name, title, mobile number and email address on the back.

Target Market(s)

Facility managers and commercial/industrial building owners/occupiers.

Contact Information for Business Card

Font styles to use
Sans Serif

Requirements
Must have
• Please only submit 5 of your best samples.
Darker tones are preferred.
Nice to have
• We want to use, black, red and grey. Keep it modern and clean.
I've attached the company logo and a sample of a boarder we use on our emergency plans.
Should not have
• No preference. Let the designer choose.

```html
<!DOCTYPE html>
<html lang="en">
<head>
<meta charset="utf-8">
<title>Tandem Hearth Works Pty Ltd — Business Card</title>
<link rel="stylesheet" href="https://fonts.googleapis.com/css2?family=Arimo:wght@400;700&family=Bebas+Neue&family=Work+Sans:wght@400&display=swap">
<style>
  :root {
    --backdrop: #434343;
    --brand-red: #ed1c24;
    --ink: #231f20;
    --paper: #ffffff;
  }
  * { margin: 0; padding: 0; box-sizing: border-box; }
  html, body { width: 1013px; height: 1200px; overflow: hidden; }
  body { background: var(--backdrop); position: relative; font-family: "Arimo", Arial, sans-serif; }

  .card { position: absolute; left: 211px; width: 591px; height: 337px; overflow: hidden; }
  .card--front { top: 237px; background: var(--paper); }
  .card--back { top: 640px; background: var(--brand-red); color: var(--paper); }

  /* Front */
  .brand-mark {
    position: absolute; left: 66px; top: 104px; width: 160px;
    font-family: "Arimo", Arial, sans-serif; font-weight: 700; font-size: 76px;
    line-height: 76px; letter-spacing: -2px; color: var(--brand-red);
  }
  .divider { position: absolute; left: 295px; top: 82px; width: 1px; height: 123px; background: var(--brand-red); }
  .divider::before { content: ""; position: absolute; left: 0; top: 0; width: 3px; height: 20px; background: var(--brand-red); }
  .person { position: absolute; left: 334px; top: 82px; }
  .person__name { font-family: "Bebas Neue", "Oswald", sans-serif; font-size: 31px; line-height: 28px; color: var(--brand-red); letter-spacing: 0.2px; }
  .person__title { font-family: "Work Sans", sans-serif; font-size: 15px; line-height: 18px; color: var(--ink); }
  .contact-list { position: absolute; left: 334px; top: 148px; list-style: none; font-family: "Work Sans", sans-serif; font-size: 15.5px; color: var(--ink); }
  .contact-list li { display: flex; align-items: center; height: 19.5px; }
  .contact-list svg { width: 11px; height: 11px; margin-right: 8px; fill: var(--brand-red); }
  .swoosh { position: absolute; left: 0; top: 0; width: 591px; height: 337px; }

  /* Back */
  .back-mark {
    position: absolute; left: 0; right: 0; top: 58px; text-align: center;
    font-weight: 700; font-size: 98px; line-height: 110px; letter-spacing: -3px;
  }
  .company-name { position: absolute; left: 0; right: 0; top: 189px; text-align: center; font-size: 32px; line-height: 40px; }
  .web-line { position: absolute; left: 0; right: 0; top: 248px; display: flex; justify-content: center; align-items: center; gap: 6px; font-size: 18.5px; }
  .web-line .rule { width: 65px; height: 1px; background: linear-gradient(90deg, rgba(255,200,120,0), #fff); }
  .web-line .rule--right { background: linear-gradient(90deg, #fff, rgba(255,200,120,0)); }
  .office-phone { position: absolute; left: 0; right: 0; top: 282px; display: flex; justify-content: center; align-items: center; gap: 4px; font-size: 20px; }
  .office-phone svg { width: 19px; height: 19px; }
</style>
</head>
<body>
  <section class="card card--front">
    <div class="brand-mark">THW</div>
    <div class="divider"></div>
    <div class="person">
      <h1 class="person__name">Daniel Harper</h1>
      <p class="person__title">Manager</p>
    </div>
    <ul class="contact-list">
      <li>
        <svg viewBox="0 0 24 24"><path d="M6.6 10.8a15.1 15.1 0 0 0 6.6 6.6l2.2-2.2c.3-.3.7-.4 1-.2 1.1.4 2.3.6 3.6.6.6 0 1 .4 1 1V20c0 .6-.4 1-1 1A17 17 0 0 1 3 4c0-.6.4-1 1-1h3.5c.6 0 1 .4 1 1 0 1.3.2 2.5.6 3.6.1.3 0 .7-.2 1z"/></svg>
        +1 555 014 270
      </li>
      <li>
        <svg viewBox="0 0 24 24"><path d="M2 9l10 7 10-7v12H2z"/><path d="M5 3h14v7l-7 5-7-5z" opacity=".7"/></svg>
        danielharper@thw.com
      </li>
    </ul>
    <svg class="swoosh" viewBox="0 0 591 337" aria-hidden="true">
      <path d="M60 297 Q295 222 530 297 Q295 233 60 297Z" fill="var(--ink)"/>
      <path d="M0 322 Q295 229 591 322 V337 H0Z" fill="var(--brand-red)"/>
    </svg>
  </section>

  <section class="card card--back">
    <div class="back-mark">THW</div>
    <p class="company-name">Tandem Hearth Works Pty Ltd</p>
    <p class="web-line"><span class="rule"></span>www.tandemhearthworks.com<span class="rule rule--right"></span></p>
    <p class="office-phone">
      <svg viewBox="0 0 24 24" fill="none" stroke="#fff" stroke-width="1.8"><circle cx="12" cy="12" r="10.5"/><path d="M8.5 7h2l1 2.5-1.3 1a6 6 0 0 0 3.3 3.3l1-1.3 2.5 1v2a1 1 0 0 1-1 1A8 8 0 0 1 7.5 8a1 1 0 0 1 1-1z"/></svg>
      +0155501427
    </p>
  </section>
</body>
</html>
```